Brightmoor - a website to encourage people to spend time in nature

I have a squarespace site with some content on it but the squarespace template doesn't completely suit my needs, I keep fiddling with the template but actually I need some professional help to get it looking the way I want and with the right 'mood'.
The website is for "Brightmoor" - it will be a blog where I write about the importance of nature for good health. I also want to use the website to market services such as outdoor coaching, retreats and walking workshops.
This has been in my head for a LONG time and I currently only use instagram for micro-blogs but it's time for me to get this moving. I've previously engaged other designers on branding for it but they just didn't get it quite the way that I wanted it and I wasn't completely happy with the results. It's been a process for me as to what I want but in the meantime I just didn't come back to the design aspect of it now. I'm looking for a designer who understands the purpose of the website, the ethos and can help me realise this into a design that's clean, clear and simple.

Please note that I have a domain (brightmoor.org) and a lot of content drafted on squarespace already. I have published it with password protection - password is brightmoor2020 - it still has some of the original template on it, but does have some content. Don't take it as anything to follow in particular, i am looking for fresh eyes and fresh ideas.

Target Market(s)

There are three main groups that I want to target - people who are suffering from stress and anxiety, people who treat them and parents who want to get their kids outside (thereby preventing stress and anxiety)

Contact Information for Business Card

Joan Petrie
Brightmoor
Telephone +44 7700 900417
brightmoor@mailvane.com

Logo Text

Brightmoor - if that. I have an idea that the logo should have a leaf on it somewhere, or maybe just be a leaf.

Coding

Coded - Design and coding required

Number of Pages Required

5+ page

Font styles to use
Serif
Sans Serif

Colors
add136
33b8a4
34a6d7
3377b5

Requirements
Must have
• Space for lots of images. The ability for me to edit the pages if I need to. Be user friendly. Look beautiful.
• For an idea of the images I use and the content I'm interested in writing about have a look at @brightmoor on instagram.
• That pop up about cookies so I am complying with data laws.
Should not have
• Must not be too 'busy' I'd like to avoid too much movement.

```html
<!DOCTYPE html>
<html lang="en">
<head>
<meta charset="utf-8">
<title>Brightmoor</title>
<link href="https://fonts.googleapis.com/css2?family=Delius&family=Itim&family=Montserrat:wght@400;500;600&display=swap" rel="stylesheet">
<style>
:root{
  --mint:#9cdcd0;
  --mint-soft:#a8ddd6;
  --paper:#f6f6f6;
  --pale:#e3f0ef;
  --pale-blog:#d6ebe8;
  --blue:#3377b5;
  --blue-soft:#5a97c8;
  --lime:#add136;
  --ink:#222;
  --grey:#777;
  --dark:#2d2d2d;
}
*{box-sizing:border-box;margin:0;padding:0}
html,body{width:1200px;height:3933px;overflow:hidden;background:var(--paper)}
body{position:relative;font-family:"Montserrat",sans-serif;color:var(--ink)}
.abs{position:absolute}
.display{font-family:"Delius",cursive}
.hand{font-family:"Itim",cursive}
.topbar{left:0;top:0;width:1200px;height:35px;background:var(--mint)}
.dot{display:inline-block;width:9px;height:9px;border-radius:50%;background:#2a3a3a;margin-right:8px}
.masthead{left:0;top:35px;width:1200px;height:154px;background:var(--paper);text-align:center}
.masthead h1{font-family:"Delius",cursive;font-weight:400;font-size:54px;margin-top:28px;letter-spacing:1px}
.masthead p{font-size:13px;color:var(--grey);margin-top:4px}
.leaf-fill{background:radial-gradient(circle,#d5dcd4,transparent 70%)}
.hero{left:0;top:189px;width:1200px;height:494px;background:var(--pale)}
.photo{border-radius:2px}
.hero-main{left:61px;top:223px;width:695px;height:426px;background:linear-gradient(120deg,#c78aa3,#d9b8a0 45%,#8a7a5e)}
.hero-main h2{position:absolute;left:25px;font-family:"Delius",cursive;font-weight:400;color:#fff}
.video{left:776px;top:223px;width:320px;height:203px;background:linear-gradient(160deg,#9fcc6a,#dfe6d8 50%,#7aa04a)}
.video-tag{position:absolute;left:0;top:0;width:124px;height:72px;background:rgba(173,209,54,.85);color:#fff;padding:8px 10px;font-family:"Delius",cursive;letter-spacing:3px;line-height:1}
.more-blogs{left:776px;top:446px;width:320px;height:203px;background:var(--blue);color:#fff;font-family:"Delius",cursive;font-size:30px;letter-spacing:4px;display:flex;align-items:center;justify-content:center}
.side-social{left:0;top:476px;width:43px;height:173px;background:#fff;display:flex;flex-direction:column;align-items:center;justify-content:center;gap:20px}
.side-social span{width:10px;height:10px;border-radius:50%;background:#333}
.subscribe-box{left:137px;top:730px;width:926px;height:182px;background:var(--mint-soft)}
.sub-title{font-family:"Delius",cursive;font-size:38px;letter-spacing:4px;line-height:1}
.sub-kicker{font-size:13px;letter-spacing:3px;color:var(--blue);font-family:"Delius",cursive}
.field{background:#fff;border-radius:4px;color:#bbb;font-size:13px;padding:0 28px;display:flex;align-items:center}
.btn{background:var(--blue);color:#fff;border-radius:4px;font-size:13px;letter-spacing:2px;font-weight:600;display:flex;align-items:center;justify-content:center;box-shadow:0 3px 6px rgba(0,0,0,.2)}
.intro-line{left:0;top:975px;width:508px;height:4px;background:var(--blue)}
.intro-card{left:0;top:993px;width:850px;height:238px;background:var(--pale);border-radius:0 6px 6px 0}
.intro-block{left:850px;top:968px;width:350px;height:289px;background:var(--blue)}
.intro-pane{left:850px;top:993px;width:88px;height:238px;background:var(--blue-soft);border-radius:0 6px 6px 0}
.avatar{left:66px;top:1024px;width:176px;height:176px;border-radius:50%;background:linear-gradient(150deg,#e9e2d2,#9a8f80 60%,#2a2a2a)}
.h-section{font-family:"Delius",cursive;font-weight:400;text-align:center;width:1200px;left:0}
.about{left:0;top:1422px;width:1200px;height:646px;background:var(--pale)}
.origin{left:96px;top:1489px;width:504px;height:502px;background:linear-gradient(180deg,#4f86c4,#6e9cc9 55%,#5f87ad);border-radius:3px;color:#fff;padding:110px 54px 0}
.origin h3{font-family:"Delius",cursive;font-weight:400;font-size:30px}
.origin .lead{font-size:17px;letter-spacing:1.5px;margin:16px 0 12px}
.origin p.body{font-size:13.5px;letter-spacing:1.5px;line-height:23px}
.btn-white{background:#fff;color:var(--blue);border-radius:4px;width:144px;height:40px;display:flex;align-items:center;justify-content:center;font-size:13px;letter-spacing:2px;font-weight:600;margin-top:16px}
.about-item h3{font-family:"Delius",cursive;font-weight:400;font-size:29px}
.about-item p{font-size:13.5px;color:var(--grey);letter-spacing:2px;line-height:23px;margin:14px 0 18px}
.about-item .btn{height:38px;font-size:11px}
.blogs{left:0;top:2068px;width:1200px;height:1298px;background:var(--pale-blog)}
.tile{overflow:hidden;border-radius:22px}
.tile-label{position:absolute;color:#fff;text-align:center;font-family:"Itim",cursive;text-shadow:0 1px 3px rgba(0,0,0,.25)}
.tile-label .t{font-size:31px;line-height:36px}
.tile-label .d{font-size:20px;margin-top:6px}
.tile-label .rule{width:32px;height:2px;background:rgba(255,255,255,.8);margin:14px auto 0}
.contact{left:0;top:3366px;width:1200px;height:281px;background:var(--paper)}
.footer{left:0;top:3647px;width:1200px;height:219px;background:var(--blue)}
.copyright{left:0;top:3866px;width:1200px;height:67px;background:var(--dark);color:#eee;font-size:14px;display:flex;align-items:center;justify-content:center;gap:10px}
</style>
</head>
<body>

<div class="abs topbar">
  <div class="abs" style="left:62px;top:13px"><span class="dot"></span><span class="dot"></span><span class="dot"></span>
    <svg width="11" height="9" viewBox="0 0 11 9" style="vertical-align:top"><rect x=".5" y=".5" width="10" height="8" fill="none" stroke="#2a3a3a"/><path d="M.5 .5l5 4 5-4" fill="none" stroke="#2a3a3a"/></svg>
  </div>
  <div class="abs" style="left:1032px;top:11px;font-size:10px;color:#444">search..</div>
  <svg class="abs" style="left:1078px;top:11px" width="12" height="12" viewBox="0 0 12 12"><circle cx="5" cy="5" r="3.8" fill="none" stroke="#333" stroke-width="1.5"/><path d="M8 8l3.5 3.5" stroke="#333" stroke-width="1.5"/></svg>
  <svg class="abs" style="left:1124px;top:11px" width="15" height="12" viewBox="0 0 15 12"><path d="M0 2h15M0 6h15M0 10h15" stroke="#222" stroke-width="2"/></svg>
</div>

<header class="abs masthead">
  <div class="abs leaf-fill" role="img" aria-label="Soft watercolour leaves and blossoms" style="left:0;top:0;width:200px;height:150px"></div>
  <div class="abs leaf-fill" role="img" aria-label="Faint pink blossom wash" style="left:380px;top:0;width:500px;height:60px;background:radial-gradient(ellipse,#f3dfe4,transparent 70%)"></div>
  <h1>Brightmoor</h1>
  <p>The practice of spending time in nature to feel better.</p>
</header>

<section class="abs hero">
  <div class="abs side-social" style="top:287px"><span></span><span></span><span></span>
    <svg width="11" height="9" viewBox="0 0 11 9"><rect x=".5" y=".5" width="10" height="8" fill="none" stroke="#333"/><path d="M.5 .5l5 4 5-4" fill="none" stroke="#333"/></svg>
  </div>
</section>
<div class="abs photo hero-main" role="img" aria-label="Smiling woman on a bicycle among pink flowering shrubs">
  <h2 style="top:50px;font-size:30px">Welcome To</h2>
  <h2 style="top:82px;font-size:52px">Brightmoor</h2>
</div>
<div class="abs photo video" role="img" aria-label="Two children lying in a meadow of daisies">
  <div class="video-tag"><div style="font-size:27px">Video</div><div style="font-size:20px">Blogs</div></div>
  <svg class="abs" style="right:18px;bottom:10px" width="34" height="34" viewBox="0 0 34 34"><circle cx="17" cy="17" r="15" fill="none" stroke="#fff" stroke-width="2"/><path d="M13 10l11 7-11 7z" fill="none" stroke="#fff" stroke-width="2"/></svg>
</div>
<div class="abs more-blogs">More Blogs</div>

<div class="abs subscribe-box">
  <div class="abs" style="left:90px;top:58px">
    <div class="sub-title">Subscribe</div>
    <div class="sub-kicker" style="margin-top:4px">Stay Connected</div>
  </div>
  <div class="abs field" style="left:324px;top:70px;width:384px;height:41px">Email</div>
  <div class="abs btn" style="left:722px;top:70px;width:122px;height:41px">Sign up</div>
</div>

<div class="abs intro-line"></div>
<div class="abs intro-block"></div>
<div class="abs intro-card"></div>
<div class="abs intro-pane"></div>
<div class="abs avatar" role="img" aria-label="Portrait of the blogger in sunglasses"></div>
<div class="abs" style="left:275px;top:1093px">
  <div class="display" style="font-size:16px;letter-spacing:1.5px">Welcome to Brightmoor.</div>
  <div style="font-size:13px;color:#555;letter-spacing:1px;margin-top:8px">I document the relationship between nature and better health.</div>
  <span class="dot" style="margin-top:12px;width:13px;height:13px"></span>
</div>
<div class="abs leaf-fill" role="img" aria-label="Faint grey leaf sprigs" style="left:1020px;top:1257px;width:180px;height:140px"></div>

<h2 class="abs h-section" style="top:1302px;font-size:54px">About Us</h2>

<section class="abs about"></section>
<div class="abs origin">
  <div class="abs" role="img" aria-label="Person seen from behind looking out to sea" style="inset:0;background:linear-gradient(180deg,rgba(120,150,180,.25),rgba(60,80,110,.35));border-radius:3px"></div>
  <div style="position:relative">
    <h3>Origin Story</h3>
    <div class="lead">In The Beginning...</div>
    <p class="body">Brightmoor Was Founded In 2017 By Me, Joan Petrie, A Recovering Lawyer/Corporate Junkie. I Had Spent Most Of The Previous Fifteen Years In Offices In London And For Many Of Those Years I Had Been Sedantry, Stressed And Ill-At-Ease With Myself.</p>
    <div class="btn-white">Read More</div>
  </div>
</div>
<div class="abs photo" role="img" aria-label="Pink cherry blossom close up" style="left:618px;top:1489px;width:181px;height:244px;background:linear-gradient(140deg,#e27fa6,#f4c5d6 50%,#b24f76)"></div>
<div class="abs photo" role="img" aria-label="Small dog and long shadow on an empty beach" style="left:618px;top:1748px;width:181px;height:243px;background:linear-gradient(180deg,#7fa6d6,#cfdbe8 42%,#5a534a 50%,#3e3a34)"></div>
<div class="abs about-item" style="left:826px;top:1533px">
  <h3>What We Do</h3>
  <p>We Do Some Things That Will<br>Help You Get Back To Nature.</p>
  <div class="btn" style="width:122px">Read More</div>
</div>
<div class="abs about-item" style="left:828px;top:1765px">
  <h3>Partners</h3>
  <p>We Believe We Work Better When<br>We Work Together.&nbsp; We Are Proud<br>To Work Together With These<br>Organisations.</p>
  <div class="btn" style="width:135px;height:42px">Read More</div>
</div>

<section class="abs blogs">
  <h2 class="abs h-section" style="top:48px;font-size:54px">Blogs</h2>
  <div class="abs hand" style="left:0;width:1200px;text-align:center;top:138px;font-size:30px;color:var(--blue)">Good for you. Good for the plannet</div>
</section>

<div class="abs tile" role="img" aria-label="Smiling woman in glasses holding a striped scarf at a street cafe" style="left:61px;top:2339px;width:622px;height:468px;border-radius:22px 22px 22px 0;background:linear-gradient(90deg,#b9a87e,#6b5a4a 60%,#3d332c)">
  <div class="abs" style="left:0;top:0;width:298px;height:468px;background:rgba(173,209,54,.82);border-radius:22px"></div>
  <div class="tile-label" style="left:0;width:298px;top:186px"><div class="t">On the Verge</div><div class="d">Aug 8</div><div class="rule"></div></div>
</div>
<div class="abs tile" role="img" aria-label="Nest of feathers with small eggs on grass" style="left:684px;top:2339px;width:455px;height:303px;background:linear-gradient(90deg,#c8c8c0,#9aa58a 40%,#6a9a2a)">
  <div class="abs" style="left:207px;top:0;width:248px;height:303px;background:rgba(173,209,54,.82);border-radius:22px"></div>
  <div class="tile-label" style="left:207px;width:248px;top:98px"><div class="t">Notes From<br>the Nest</div><div class="d">Jun 17</div><div class="rule"></div></div>
</div>
<div class="abs tile" role="img" aria-label="Path through a sunlit green forest" style="left:684px;top:2645px;width:309px;height:401px;background:linear-gradient(180deg,#9bbf54,#4a6a2a 55%,#6a8a3a)">
  <div class="abs" style="left:0;top:0;width:309px;height:185px;background:rgba(173,209,54,.82);border-radius:22px 22px 0 22px"></div>
  <div class="tile-label" style="left:0;width:309px;top:50px"><div class="t">Coming Home<br>to the Woods</div><div class="d">Jun 17</div><div class="rule"></div></div>
</div>
<div class="abs tile" style="left:994px;top:2645px;width:145px;height:401px;background:var(--blue);color:#fff;font-family:'Itim',cursive;font-size:29px;line-height:36px;padding:150px 0 0 28px">
  For<br>More
  <svg width="68" height="12" viewBox="0 0 68 12" style="display:block;margin-top:10px"><path d="M0 6h66M60 1l6 5-6 5" fill="none" stroke="#fff" stroke-width="2"/></svg>
</div>
<div class="abs tile" role="img" aria-label="Pocket watch floating in a blue sky with clouds" style="left:61px;top:2807px;width:622px;height:467px;border-radius:0 0 22px 22px;background:linear-gradient(160deg,#3f6fb0,#9bb9dc 55%,#e8eef5)">
  <div class="abs" style="left:0;top:313px;width:622px;height:154px;background:rgba(173,209,54,.9);border-radius:22px"></div>
  <div class="tile-label" style="left:0;width:622px;top:345px"><div class="t">Skytime Over Screentime</div><div class="d">Jun 17</div><div class="rule"></div></div>
</div>
<div class="abs tile" role="img" aria-label="Earth horizon glowing from space" style="left:684px;top:3049px;width:455px;height:225px;background:linear-gradient(180deg,#6b8a2a,#3a6a8a 70%,#111)">
  <div class="abs" style="left:0;top:0;width:455px;height:163px;background:rgba(130,160,40,.9);border-radius:22px"></div>
  <div class="tile-label" style="left:0;width:455px;top:24px"><div class="t">In The Beginning<br>There Was Thunder</div><div class="d">Jun 17</div><div class="rule"></div></div>
</div>

<section class="abs contact">
  <h2 class="abs h-section" style="top:40px;font-size:54px">Contact us</h2>
  <div class="abs" style="left:0;width:1200px;text-align:center;top:130px;font-size:13px;color:var(--grey);letter-spacing:2px">Email Me For Press/Media Inquiries And Other Collaborations.</div>
  <div class="abs btn" style="left:388px;top:181px;width:426px;height:40px;letter-spacing:2px">hello@brightmoor.org</div>
</section>

<footer class="abs footer">
  <div class="abs" style="left:62px;top:94px">
    <div class="sub-title" style="font-size:36px">Subscribe</div>
    <div class="sub-kicker" style="color:#fff;margin-top:2px">Stay Connected</div>
  </div>
  <div class="abs field" style="left:296px;top:91px;width:384px;height:40px">Email</div>
  <div class="abs btn" style="left:695px;top:91px;width:122px;height:40px">Sign up</div>
  <div class="abs" style="left:1026px;top:180px;display:flex;gap:14px;align-items:center">
    <span class="dot" style="background:#fff;margin:0;width:14px;height:14px"></span>
    <span class="dot" style="background:#fff;margin:0;width:14px;height:14px"></span>
    <span class="dot" style="background:#fff;margin:0;width:14px;height:14px"></span>
    <svg width="18" height="13" viewBox="0 0 18 13"><rect x=".75" y=".75" width="16.5" height="11.5" fill="none" stroke="#fff" stroke-width="1.5"/><path d="M.75 .75l8.25 6 8.25-6" fill="none" stroke="#fff" stroke-width="1.5"/></svg>
  </div>
</footer>

<div class="abs copyright">
  <svg width="20" height="20" viewBox="0 0 20 20"><circle cx="10" cy="10" r="8.5" fill="none" stroke="#eee" stroke-width="1.5"/><path d="M13 7.5a3.6 3.6 0 1 0 0 5" fill="none" stroke="#eee" stroke-width="1.5"/></svg>
  <span>Copyright@Brightmoor2019</span>
</div>

</body>
</html>
```